International business needs business cards

Our company, DRV Ventures Inc. is in the business of supplying a range construction products with particular emphasis on CEMENT. We have developed our own brand - TORVAN SUPPLIES - with which to infiltrate the market. We are launching our brand of cement (TORVAN Type IS Cement) into the Caribbean which is unlike anything this market has ever seen. A monopoly has existed here for the past 60-odd years and the market has now opened to allow the importation of other brands and consumers are anxious and ready for change/improvement. We are very excited to be launching and want to make a great first impression. We will be conducting workshops and seminars (from government level to the hardware store owners) and we want our business card to give us the strong, confident introduction that we need.

Target Market(s)

construction; builders; engineers; home owners

Industry/Entity Type

Construction

Contact Information for Business Card

Marisol Depree
CEO
cell # 1 555 4180736
Ground floor,Lindell Plaza Suite 2734
George Town,Grand Cayman
Cayman Islands,KY1-4823
EMAIL: m.depree@drvventuresinc.example
web site drvventuresinc.example

COMPANY: skype info drv.ventures.example

second card
Yvette Brannock-Depree
CFO
CELL# 1 555 607 3941
George Town,Grand Cayman
Cayman Islands,KY1-4823
EMAIL: y.brannockdepree@drvventuresinc.example
website drvventuresinc.example

Requirements
Must have
• Business cards must display BOTH logos - DRV is the company and TORVAN is the brand.

```html
<!DOCTYPE html>
<html lang="en">
<head>
<meta charset="utf-8">
<title>DRV Ventures Inc. – Business Card</title>
<link rel="stylesheet" href="https://fonts.googleapis.com/css2?family=Open+Sans:wght@400;600;700&display=swap">
<style>
  :root{
    --stage:#e9e6e1;
    --card-black:#0c0c0c;
    --brand-red:#8e1a1f;
    --tan:#b38a6a;
    --ink:#1a1a1a;
    --white:#ffffff;
    --grey:#6b6b6b;
  }
  *{box-sizing:border-box;margin:0;padding:0}
  html,body{width:1200px;height:950px;overflow:hidden}
  body{background:var(--stage);font-family:"Open Sans",Arial,sans-serif;position:relative}

  .card{position:absolute;left:250px;width:700px;height:400px;overflow:hidden;
        box-shadow:0 6px 18px rgba(0,0,0,.25)}
  .card-back{top:50px;background:linear-gradient(160deg,#1f1f1f 0%,var(--card-black) 55%)}
  .card-front{top:500px;background:var(--white)}

  /* back */
  .back-mark{position:absolute;left:0;right:0;top:130px;display:flex;align-items:center;justify-content:center;gap:16px}
  .mark-square{width:56px;height:56px;background:var(--brand-red)}
  .back-name{color:var(--white);font-weight:700;font-size:34px;letter-spacing:.5px}
  .back-web{position:absolute;left:0;right:0;top:262px;text-align:center;color:var(--white);
            font-size:17px;letter-spacing:4px}

  /* front */
  .wave{position:absolute;inset:0;width:700px;height:400px}
  .company-mark{position:absolute;left:40px;top:92px;display:flex;align-items:center;gap:12px}
  .company-mark .mark-square{width:44px;height:44px}
  .company-name{font-weight:700;font-size:26px;color:var(--ink)}
  .brand-mark{position:absolute;left:70px;top:195px;display:flex;align-items:center;gap:10px}
  .brand-circle{width:26px;height:26px;border-radius:50%;background:var(--grey)}
  .brand-name{font-weight:700;font-size:20px;color:var(--grey);letter-spacing:1px}

  .contact{position:absolute;right:30px;top:62px;text-align:right;color:var(--white);font-size:14px;line-height:1.45}
  .contact .person{font-weight:700;font-size:22px;line-height:1.2}
  .contact .role{font-size:14px;margin-bottom:8px}
  .contact .line{display:flex;justify-content:flex-end;align-items:center;gap:8px}
  .icon{width:14px;height:14px;flex:none}
</style>
</head>
<body>

<section class="card card-back" aria-label="Card back">
  <div class="back-mark">
    <div class="mark-square"></div>
    <span class="back-name">DRV Ventures Inc.</span>
  </div>
  <p class="back-web">www.drvventuresinc.example</p>
</section>

<section class="card card-front" aria-label="Card front">
  <svg class="wave" viewBox="0 0 700 400" aria-hidden="true">
    <g>
      <path transform="translate(-16,-10)" fill="var(--tan)" d="M360 0 C430 70 400 200 300 270 C210 330 100 350 0 355 L0 400 L700 400 L700 0 Z"/>
      <path transform="translate(-10,-5)" fill="var(--ink)" d="M360 0 C430 70 400 200 300 270 C210 330 100 350 0 355 L0 400 L700 400 L700 0 Z"/>
      <path transform="translate(-5,-2)" fill="var(--white)" d="M360 0 C430 70 400 200 300 270 C210 330 100 350 0 355 L0 400 L700 400 L700 0 Z"/>
      <path fill="var(--brand-red)" d="M360 0 C430 70 400 200 300 270 C210 330 100 350 0 355 L0 400 L700 400 L700 0 Z"/>
    </g>
  </svg>

  <div class="company-mark">
    <div class="mark-square"></div>
    <span class="company-name">DRV Ventures Inc.</span>
  </div>

  <div class="brand-mark">
    <div class="brand-circle"></div>
    <span class="brand-name">TORVAN SUPPLIES</span>
  </div>

  <div class="contact">
    <p class="person">Marisol Depree</p>
    <p class="role">CEO</p>
    <p>Ground floor</p>
    <p>Lindell Plaza Suite 2734</p>
    <p>George Town,Grand Cayman</p>
    <p class="line">Cayman Islands,KY1-4823
      <svg class="icon" viewBox="0 0 14 14" aria-hidden="true"><rect x="3" y="0.5" width="8" height="13" rx="1.5" fill="none" stroke="#fff" stroke-width="1.4"/><circle cx="7" cy="11" r="0.9" fill="#fff"/></svg>
    </p>
    <p class="line">1 555 4180736
      <svg class="icon" viewBox="0 0 14 14" aria-hidden="true"><rect x="0.5" y="2.5" width="13" height="9" rx="1" fill="#fff"/><path d="M1 3 L7 8 L13 3" fill="none" stroke="var(--brand-red)" stroke-width="1.2"/></svg>
    </p>
    <p class="line">m.depree@drvventuresinc.example
      <svg class="icon" viewBox="0 0 14 14" aria-hidden="true"><circle cx="7" cy="7" r="6" fill="#fff"/><path d="M1 7 H13 M7 1 C4 4 4 10 7 13 C10 10 10 4 7 1" fill="none" stroke="var(--brand-red)" stroke-width="1"/></svg>
    </p>
    <p>drvventuresinc.example</p>
  </div>
</section>

</body>
</html>
```